Career Development Skills | Business Card & Logo Design

We are looking for a business card including logo design for a new Sydney based business called 'Bright Pathwork'.
We offer a range of services that focus on building the Employability or Employment skills for individuals focusing on job seekers and those interested in building skills required to develop their career. Employability skills are required not only to gain employment, but also to progress within an organisation so as to achieve one's potential.
Updates
Target Market(s)
Our client targets include corporates and govt agencies looking to build skills within their current employee base or assist staff in the transition between roles or workplaces.
Industry/Entity Type
Business
Look and feel
Each slider illustrates characteristics of the customer's brand and the style your logo design should communicate.

```html
<!DOCTYPE html>
<html lang="en">
<head>
<meta charset="utf-8">
<title>Bright Pathwork – Business Card</title>
<link rel="stylesheet" href="https://fonts.googleapis.com/css2?family=Oswald:wght@300;400&display=swap">
<style>
  :root {
    --stage: #1b1b1b;
    --front-light: #2e2e2e;
    --front-dark: #0e0e0e;
    --back-light: #fbfbfb;
    --back-dark: #c4c4c4;
    --teal: #1c9ea6;
    --ink: #4a4a4a;
    --rule: #9a9a9a;
    --mark-grey: #a9a9a9;
  }
  * { margin: 0; padding: 0; box-sizing: border-box; }
  html, body {
    width: 1200px; height: 1164px; overflow: hidden;
    background: var(--stage);
    font-family: "Oswald", "Arial Narrow", sans-serif;
  }
  .canvas { position: relative; width: 1200px; height: 1164px; }

  .card { position: absolute; width: 724px; height: 441px; }

  .card-front {
    left: 76px; top: 107px;
    background: radial-gradient(ellipse at 50% 62%, var(--front-light) 0%, var(--front-dark) 85%);
  }
  .brand-dot {
    position: absolute; left: 324px; top: 140px;
    width: 72px; height: 72px; border-radius: 50%;
    background: #f2f2f2;
  }
  .brand-rule {
    position: absolute; left: 157px; top: 261px; width: 423px; height: 1px;
    background: linear-gradient(90deg, transparent, var(--rule) 20%, var(--rule) 80%, transparent);
  }
  .brand-name {
    position: absolute; left: 0; right: 0; top: 276px;
    text-align: center; color: var(--teal);
    font-weight: 400; font-size: 28px; letter-spacing: 4px; text-transform: uppercase;
  }

  .card-back {
    left: 384px; top: 605px;
    background: radial-gradient(ellipse at 45% 42%, var(--back-light) 0%, var(--back-dark) 95%);
  }
  .accent-line {
    position: absolute; left: 158px; top: 102px; width: 2px; height: 247px;
    background: var(--teal);
  }
  .details {
    position: absolute; left: 187px; top: 100px;
    font-weight: 300; font-size: 16px; line-height: 21px; color: var(--ink);
  }
  .details .contact { color: var(--teal); }
  .details address { font-style: normal; margin-top: 28px; }
  .phones { margin-top: 40px; color: var(--ink); }
  .phones .label { color: var(--teal); }
  .phones .dash { color: var(--teal); letter-spacing: 1px; }
  .back-name {
    position: absolute; left: 510px; top: 70px;
    color: var(--mark-grey); font-weight: 400; font-size: 28px;
  }
</style>
</head>
<body>
<div class="canvas">
  <section class="card card-front" aria-label="Business card front">
    <span class="brand-dot" aria-hidden="true"></span>
    <span class="brand-rule" aria-hidden="true"></span>
    <h1 class="brand-name">Bright Pathwork</h1>
  </section>

  <section class="card card-back" aria-label="Business card back">
    <span class="accent-line" aria-hidden="true"></span>
    <div class="details">
      <p class="contact">Daniel Hollis - Director</p>
      <p class="contact">Brightpathwork.com.au</p>
      <p class="contact">Daniel@brightpathwork.com.au</p>
      <address>
        Level 14<br>
        Harbourline Tower 3<br>
        118&nbsp;&nbsp;&nbsp;Carver Street<br>
        Harbourline, Sydney 2000
      </address>
      <div class="phones">
        <p><span class="label">Tell</span> <span class="dash">---------------</span>(02)&nbsp; 5550 1234</p>
        <p><span class="label">Fax</span> <span class="dash">---------------</span> (02)&nbsp; 5550 1299</p>
      </div>
    </div>
    <p class="back-name">Bright Pathwork</p>
  </section>
</div>
</body>
</html>
```